Business Card Design Project

Doctor, Pain Management. Need a new business card design with appointment info on the back. New address is 18 Corvell Road, Suite 304, Brisdale, NJ 07391. Right now I believe the rest of the information is staying the same.

```html
<!DOCTYPE html>
<html lang="en">
<head>
<meta charset="utf-8">
<title>Kindred Pain Management – Business Card</title>
<link href="https://fonts.googleapis.com/css2?family=Libre+Baskerville:wght@400;700&family=Tinos:wght@400;700&family=Montserrat:wght@500&display=swap" rel="stylesheet">
<style>
  :root {
    --ink: #0b0b0b;
    --yellow: #ecec3a;
    --paper: #ececec;
    --grey: #c4c4c4;
    --white: #ffffff;
    --stage: #2a2a2a;
    --muted: #cfcfcf;
  }
  * { box-sizing: border-box; margin: 0; padding: 0; }
  html, body { width: 1200px; height: 923px; overflow: hidden; background: var(--stage); }
  .stage { position: relative; width: 1200px; height: 923px; }
  .card { position: absolute; width: 540px; height: 315px; top: 304px; overflow: hidden; box-shadow: 0 10px 30px rgba(0,0,0,.45); }
  .card-back { left: 40px; background: var(--paper); color: var(--ink); font-family: "Tinos", serif; }
  .card-front { left: 620px; background: var(--ink); font-family: "Tinos", serif; }

  /* back: appointment */
  .appt-header { position: absolute; left: 0; top: 0; width: 100%; height: 46px; background: var(--yellow); border-bottom: 4px solid var(--ink); display: flex; align-items: center; justify-content: space-between; padding: 0 22px; }
  .appt-contact { font-size: 15px; font-weight: 700; }
  .appt-contact span { font-weight: 400; }
  .appt-title { font-family: "Libre Baskerville", serif; font-weight: 700; font-size: 24px; }
  .appt-row { position: absolute; left: 36px; right: 36px; display: flex; align-items: flex-end; font-size: 18px; gap: 8px; }
  .appt-line { flex: 1; border-bottom: 1px solid var(--ink); height: 1px; margin-bottom: 4px; }
  .row-for { top: 70px; }
  .row-days { top: 112px; justify-content: space-between; }
  .day::before { content: ""; display: inline-block; width: 13px; height: 13px; border: 1px solid var(--ink); margin-right: 4px; vertical-align: -1px; }
  .row-date { top: 156px; }
  .row-date .appt-line { flex: 1.4; }
  .row-date .time-label { margin-left: 14px; }
  .appt-note { position: absolute; top: 200px; left: 60px; right: 60px; text-align: center; font-size: 15px; font-weight: 700; line-height: 1.3; }
  .appt-footer { position: absolute; left: 0; bottom: 0; width: 100%; height: 38px; background: var(--ink); color: var(--yellow); font-family: "Montserrat", sans-serif; font-size: 14px; display: flex; align-items: center; padding-left: 34px; }

  /* front: identity */
  .front-art { position: absolute; inset: 0; }
  .practice-name { position: absolute; top: 26px; left: 0; width: 100%; text-align: center; color: var(--yellow); font-size: 40px; font-weight: 400; letter-spacing: .5px; }
  .doctor { position: absolute; left: 40px; top: 112px; width: 218px; text-align: right; }
  .doctor-name { color: var(--white); font-weight: 700; font-size: 24px; }
  .doctor-creds { color: var(--yellow); font-size: 17px; margin-top: 2px; }
  .divider { position: absolute; left: 278px; top: 90px; width: 2px; height: 112px; background: #555; }
  .contact-list { position: absolute; left: 298px; top: 94px; list-style: none; color: var(--muted); font-size: 15px; line-height: 24px; }
  .contact-list li { display: flex; align-items: center; gap: 8px; }
  .icon { width: 14px; height: 14px; flex: none; }
</style>
</head>
<body>
<main class="stage">

  <section class="card card-back" aria-label="Appointment card">
    <header class="appt-header">
      <p class="appt-contact">P: <span>(555) 214-3870</span></p>
      <h2 class="appt-title">Appointment</h2>
      <p class="appt-contact">F: <span>(555) 214-3871</span></p>
    </header>
    <div class="appt-row row-for"><span>For:</span><span class="appt-line"></span></div>
    <div class="appt-row row-days">
      <span class="day">Mon</span><span class="day">Tue</span><span class="day">Wed</span><span class="day">Thu</span><span class="day">Fri</span><span class="day">Sat</span><span class="day">Sun</span>
    </div>
    <div class="appt-row row-date"><span>Date:</span><span class="appt-line"></span><span class="time-label">Time:</span><span class="appt-line"></span></div>
    <p class="appt-note">If you are unable to keep your appointment,<br>please give 24 hours notice.</p>
    <footer class="appt-footer">www.kindredpain.example</footer>
  </section>

  <section class="card card-front" aria-label="Business card front">
    <svg class="front-art" viewBox="0 0 540 315" width="540" height="315" aria-hidden="true">
      <defs>
        <linearGradient id="band-grey" x1="0" y1="0" x2="1" y2="0">
          <stop offset="0" stop-color="#d4d4d4"/>
          <stop offset="1" stop-color="#b9b9b9"/>
        </linearGradient>
        <path id="address-curve" d="M100,309 Q300,262 532,248"/>
      </defs>
      <path d="M30,315 Q240,236 540,212 L540,315 Z" fill="#ecec3a"/>
      <path d="M52,315 Q252,246 540,224 L540,315 Z" fill="#ffffff"/>
      <path d="M60,315 Q260,252 540,230 L540,315 Z" fill="url(#band-grey)"/>
      <text font-family="Tinos, serif" font-size="17" fill="#111">
        <textPath href="#address-curve">18 Corvell Road, Suite 304, Brisdale, NJ 07391</textPath>
      </text>
    </svg>

    <h1 class="practice-name">Kindred Pain Management</h1>

    <div class="doctor">
      <p class="doctor-name">Dr. Marlow Hensley</p>
      <p class="doctor-creds">M.D., Ph.D.</p>
    </div>

    <span class="divider"></span>

    <ul class="contact-list">
      <li>
        <svg class="icon" viewBox="0 0 14 14" aria-hidden="true"><rect width="14" height="14" fill="#ecec3a"/><path d="M4 3 L6 3 L6.5 5.5 L5.5 6.3 Q6.5 8 7.8 8.7 L8.6 7.6 L11 8.2 L11 10.2 Q6 11 3.8 5.2 Z" fill="#0b0b0b"/></svg>
        (555) 214-3870
      </li>
      <li>
        <svg class="icon" viewBox="0 0 14 14" aria-hidden="true"><rect width="14" height="14" fill="#ecec3a"/><rect x="3" y="5" width="8" height="5" fill="#0b0b0b"/><rect x="4.5" y="2.5" width="5" height="3" fill="none" stroke="#0b0b0b"/></svg>
        (555) 214-3871
      </li>
      <li>
        <svg class="icon" viewBox="0 0 14 14" aria-hidden="true"><rect width="14" height="14" fill="#ecec3a"/><rect x="2.5" y="4" width="9" height="6.5" fill="none" stroke="#0b0b0b"/><path d="M2.5 4 L7 8 L11.5 4" fill="none" stroke="#0b0b0b"/></svg>
        office@kindredpain.example
      </li>
      <li>
        <svg class="icon" viewBox="0 0 14 14" aria-hidden="true"><rect width="14" height="14" fill="#ecec3a"/><circle cx="7" cy="7" r="4.2" fill="none" stroke="#0b0b0b"/><path d="M2.8 7 H11.2 M7 2.8 V11.2" stroke="#0b0b0b" stroke-width=".8"/></svg>
        www.kindredpain.example
      </li>
    </ul>
  </section>

</main>
</body>
</html>
```